Medical Skincare services/menu/pricing Booklet 12 pages

We need produce a 12-page glossy, saddle-stitched booklet (5 1/2" tall X 81/2" wide). The booklet will be used as a services menu for a skin care salon. I have mocked up the booklet (w/ all copy) in WORD and I've provided a separate PDF of the accurate page order (see files attached). IMPORTANT: Feel free to use your creativity yet style-wise it should kinda match my wife's website colors and text style. Her clients are demanding so she wants a clean, high end, modern look (ala Apple maybe?). See her website for a frame of reference www.GlowWithMara.com
Updates

Target Market(s)

upscale female, professional women, teens with acne

Industry/Entity Type

Medical

Requirements
Must have
• the pics in the mock up are important. I've attached them here

```html
<!DOCTYPE html>
<html lang="en">
<head>
<meta charset="utf-8">
<title>Glow With Mara — Services Booklet</title>
<link rel="stylesheet" href="https://fonts.googleapis.com/css2?family=Oswald:wght@400;500;700&family=Lato:wght@400;700&family=Cormorant+Garamond:wght@500&display=swap">
<style>
:root{
  --ink:#111;
  --black:#121212;
  --blush:#fbeae3;
  --blush-soft:#fdf3ef;
  --silver:#b9b9b9;
  --grey-bg:#d9d9d9;
  --text:#222;
  --quote-mark:#aaa;
  --brand-blue:#3d8fc9;
  --white:#fff;
}
*{box-sizing:border-box;margin:0;padding:0}
html,body{width:1200px;height:1200px;overflow:hidden}
body{background:var(--grey-bg);font-family:'Lato',sans-serif;color:var(--text);position:relative}
.page{position:absolute;overflow:hidden;box-shadow:0 6px 14px rgba(0,0,0,.35);background:var(--white)}
.col-l{left:33px;width:560px}
.col-r{left:626px;width:558px}
.row-1{top:35px;height:368px}
.row-2{top:424px;height:366px}
.row-3{top:814px;height:366px}
.abs{position:absolute}
.head{font-family:'Oswald',sans-serif;font-weight:500;letter-spacing:.2px}
.photo{position:absolute}

/* cover */
.cover{background:var(--black)}
.cover-name{left:0;right:0;top:120px;text-align:center;font-family:'Oswald',sans-serif;font-weight:700;font-size:64px;letter-spacing:6px;color:var(--silver);line-height:1}
.cover-services{left:0;right:0;top:292px;text-align:center;color:var(--white);font-size:11px;line-height:13.5px}
.cover-strip{left:0;right:0;bottom:0;height:34px;background:var(--blush);text-align:center;line-height:34px;font-size:10px;letter-spacing:3px;color:var(--ink)}

/* bio */
.bio{background:var(--blush-soft)}
.bio-text{left:38px;top:26px;width:186px}
.bio-text h2{font-size:19px;line-height:23px;color:var(--ink);margin-bottom:10px}
.bio-text p{font-size:6.3px;line-height:8.4px;text-align:justify;color:var(--text)}
.bio-text h2.second{margin-top:22px}

/* testimonials */
.testi-bar{left:0;right:0;top:0;height:50px;background:linear-gradient(90deg,#8e8e8e,#f2f2f2 50%,#8e8e8e);border-bottom:2px solid #555}
.testi-bar h2{text-align:center;line-height:50px;font-family:'Oswald',sans-serif;font-weight:700;font-size:17px;color:var(--ink)}
.quote{position:absolute;font-size:7px;line-height:9.5px;color:var(--text)}
.quote:before{content:"•";position:absolute;left:-10px}
.byline{position:absolute;font-family:'Oswald',sans-serif;font-size:11px;color:var(--ink)}
.byline small{font-size:8.5px}
.byline .qm{display:block;color:var(--quote-mark);font-family:'Oswald',sans-serif;font-weight:700;font-size:24px;line-height:16px;height:16px}

/* treatment menu */
.menu-top{left:0;right:0;top:0;height:148px;border-bottom:3px solid var(--ink)}
.brand{left:206px;top:80px;font-family:'Oswald',sans-serif;font-size:32px;color:var(--brand-blue);font-weight:400;line-height:1}
.brand-tag{left:296px;top:124px;font-size:8px;color:var(--ink)}
.menu-list{left:24px;right:24px;top:178px;text-align:center}
.menu-list h3{font-family:'Oswald',sans-serif;font-size:10px;font-weight:700;color:var(--ink);margin-top:7px}
.menu-list p{font-size:7px;line-height:9.5px;color:var(--text)}
.menu-foot{left:0;right:0;bottom:0;height:14px;background:var(--black)}

/* laser */
.laser-top{left:0;right:0;top:0;height:164px;border-bottom:3px solid var(--ink)}
.laser-ghost{left:194px;top:44px;font-family:'Lato',sans-serif;font-size:46px;color:#8f97a0;letter-spacing:1px;line-height:1}
.laser-ghost span{display:block;font-size:30px;padding-left:76px;color:#a9b1ba}
.laser-caption{left:40px;top:144px;font-family:'Cormorant Garamond',serif;font-size:11.5px;letter-spacing:.4px;color:#444}
.laser-title{left:0;right:0;top:178px;text-align:center}
.laser-title h2{font-family:'Oswald',sans-serif;font-weight:700;font-size:27px;line-height:30px;color:var(--ink)}
.laser-title h3{font-family:'Oswald',sans-serif;font-weight:400;font-size:14px;color:var(--ink)}
.laser-title p{font-size:7px;line-height:9px;margin-top:6px;color:var(--text)}
.laser-price{left:0;right:0;bottom:0;height:108px;background:var(--blush)}
.price-label{position:absolute;top:7px;font-family:'Oswald',sans-serif;font-size:8px;color:var(--ink)}
.price-label b{font-size:10px}
.result{position:absolute;top:22px;width:78px;height:78px;border-radius:50%;border:3px solid #f3d2c4}

/* booking */
.booking{background:var(--black);color:var(--white)}
.booking-info{left:16px;top:14px;width:310px}
.booking-info h2{font-family:'Oswald',sans-serif;font-weight:400;font-size:17px;margin:0 0 6px}
.booking-info h2.gap{margin-top:14px}
.line{display:flex;align-items:flex-start;gap:6px;font-size:11px;font-weight:700;line-height:14.5px}
.line svg{flex:0 0 10px;margin-top:2px}
.line.pad{padding-left:16px}
.booking-name{left:16px;bottom:14px;font-family:'Oswald',sans-serif;font-weight:700;font-size:24px;color:var(--silver);letter-spacing:2px}
</style>
</head>
<body>

<!-- Cover -->
<section class="page col-l row-1 cover">
  <div class="abs cover-name">GLOW WITH MARA</div>
  <div class="abs cover-services">
    • AquaPeel Pro &nbsp;• Laser Renew &nbsp;• PL (Photo Light)<br>
    Vascular &nbsp;• Microneedling MD &nbsp;• LED Light Therapy<br>
    Vital Peel &nbsp;• Customized Facials &amp; Peels &nbsp;• Dermaplane
  </div>
  <div class="abs cover-strip">www.GlowWithMara.com</div>
</section>

<!-- Owner bio -->
<section class="page col-r row-1 bio">
  <div class="abs bio-text">
    <h2 class="head">MARA ELLISON MEDICAL AESTHETICIAN &amp; OWNER</h2>
    <p>As a teenager, I had cystic acne so bad that I would ditch school to swim in the ocean because the salt water seemed to dry out and heal my skin. I was on such a mission to clear my skin that I spent my weekly allowance on skin care products I saw on TV. Then, I memorized every ingredient. I was so intrigued by the beauty industry that, by 19, I began a career as a make up artist for Lumière, Vero, Belle Brun, Presque and Stellan. By 23, I was a skincare consultant for the Genevieve Klein Salons in Beverly Hills and Orange County California. I was honored to learn from the world's most demanding clients.</p>
    <h2 class="head second">I UNDERSTAND WHY YOUR SKIN MATTERS</h2>
    <p>Admit it. We take more pictures of ourselves than ever…and then try to "fix" our blemishes with photo filters. I understand your frustrations. Some of you know I've had a parallel career as a professional singer with dozens of network TV appearances; where the HD cameras take extreme close ups…Yikes!). I also sing the National Anthem at pro football, basketball and baseball games, where their 200 foot-wide big-screen displays constantly remind me that skin imperfections are magnified. I will help get your skin more naturally beautiful so you can use less photo filters ;-)</p>
  </div>
  <div class="photo" style="left:279px;top:0;width:279px;height:368px;background:linear-gradient(160deg,#d9cdb9,#8e8a78 45%,#6d8b8a 75%,#c9c0ad)" role="img" aria-label="Portrait of the owner in a patterned maxi dress beside a planter of flowers"></div>
</section>

<!-- Testimonials -->
<section class="page col-l row-2">
  <div class="abs testi-bar"><h2>TESTIMONIALS</h2></div>

  <p class="quote" style="left:44px;top:70px;width:240px">Mara is someone I definitely trust with my skincare needs because she truly cares about people and their issues.</p>
  <div class="byline" style="left:94px;top:96px"><span class="qm">“</span>PAIGE ROWAN<br><small>Reality TV Star</small></div>

  <p class="quote" style="left:309px;top:70px;width:210px">I have been seeing Mara for AquaPeels. Ever since my first AquaPeel my skin has had a healthy glow and texture. As an Aesthetic Professional, she helps me feel my personal best.</p>
  <div class="byline" style="left:424px;top:118px"><span class="qm">“</span>CARLA MERCER, <small>R.N.</small></div>

  <p class="quote" style="left:46px;top:180px;width:234px">Having ethnic skin I've been hesitant about having treatments but Mara immediately put me at ease. She has taught me so much about my skin and how to care for it. Each time I've left with my skin looking and feeling amazing.</p>
  <div class="byline" style="left:104px;top:228px"><span class="qm">“</span>DELIA HART - <small>Real Estate Agent</small></div>

  <p class="quote" style="left:296px;top:180px;width:222px">I have now had two facials by Mara and each time my skin feels so refreshed and new! She has also helped my teenage son who has acne. Mara knew exactly what he needed and is already getting clearer skin. Worth every penny.</p>
  <div class="byline" style="left:363px;top:228px"><span class="qm">“</span>TESSA MOORE - <small>Mother of Five</small></div>

  <p class="quote" style="left:43px;top:288px;width:480px">I've been seeing Mara on a regular basis because she always goes above and beyond to ensure that I'm comfortable. She made the experience all about me and my skincare needs. She is highly knowledgable and offers creative options to make sure I get what I need.</p>
  <div class="byline" style="left:372px;top:318px"><span class="qm">“</span>JENNA STROUD - <small>Marketing Exec.</small></div>
</section>

<!-- Facial menu -->
<section class="page col-r row-2">
  <div class="abs menu-top">
    <div class="photo" style="left:60px;top:0;width:160px;height:145px;background:linear-gradient(180deg,#f4e6dc,#e7cdbd 60%,#fbf6f2)" role="img" aria-label="Close-up beauty portrait with clear glowing skin"></div>
    <div class="photo" style="left:412px;top:14px;width:66px;height:128px;background:linear-gradient(180deg,#3a6ea5,#9cc4e0 55%,#c9d6df)" role="img" aria-label="Facial treatment machine on a wheeled stand"></div>
    <div class="abs brand">AquaPeel Pro</div>
    <div class="abs brand-tag">Clear Skin, Every Season</div>
  </div>
  <div class="abs menu-list">
    <h3>AQUAPEEL PRO is for…</h3>
    <p>Fine Lines and Wrinkles - Elasticity and Firmness - Even Skin Tone and Vibrancy - Oil and Congested skin - Enlarged Pores - Brown Spots</p>
    <h3 style="margin-top:14px">SIGNATURE AQUAPEEL $149 (30 MIN)</h3>
    <p>Deep cleanse and exfoliation, extracts, and hydrates your skin utilizing super serums filled with antioxidants, peptides and hyaluronic acid</p>
    <h3 style="margin-top:14px">AGE-REFINEMENT AQUAPEEL $175</h3>
    <p>Includes Derma Booster to reduce the appearance of fine lines and wrinkles. Plumps your skin to a youthful state.</p>
    <h3 style="margin-top:14px">PLATINUM AQUAPEEL $250</h3>
    <p>The ultimate AquaPeel Experience! Begin the detoxification process with Lymphatic Drainage. Then, the signature AquaPeel deeply cleanses, exfoliates, extracts and hydrates the skin while addressing your specific skin concern with a Booster of your choice. Treatment concludes with LED Light Therapy to reduce signs of aging.</p>
  </div>
  <div class="abs menu-foot"></div>
</section>

<!-- Laser treatment -->
<section class="page col-l row-3">
  <div class="abs laser-top" style="background:linear-gradient(90deg,#e9eef3,#f5f8fb 60%,#dfe7ee)">
    <div class="photo" style="left:0;top:0;width:180px;height:164px;background:linear-gradient(120deg,#e6c9a8,#f1dcc8 50%,#eef1f4)" role="img" aria-label="Smiling woman with smooth skin, hands near her cheek"></div>
    <div class="abs laser-ghost">LASER<span>RENEW</span></div>
    <div class="abs laser-caption">TREATMENT OF WRINKLES, LARGE PORES, SKIN TEXTURE &amp; REDNESS</div>
  </div>
  <div class="abs laser-title">
    <h2>LASER RENEW</h2>
    <h3>VASCULAR/Broken Capillaries</h3>
    <p>This is a non-ablative procedure that improves skin textures, redness/rosacea, enlarged pores, and scars w/ NO DOWNTIME.<br>(recommended every two weeks)</p>
  </div>
  <div class="abs laser-price">
    <div class="price-label" style="left:113px">Individual Treatment <b>$250</b></div>
    <div class="price-label" style="left:344px">Series Package of (6) <b>$1,275</b></div>
    <div class="result" style="left:72px;background:radial-gradient(circle at 40% 40%,#c99a86,#5a3a30)" role="img" aria-label="Before treatment skin close-up"></div>
    <div class="result" style="left:168px;background:radial-gradient(circle at 40% 40%,#d8ad98,#6a463a)" role="img" aria-label="After treatment skin close-up"></div>
    <div class="result" style="left:302px;background:radial-gradient(circle at 40% 40%,#d98f88,#3e2a28)" role="img" aria-label="Before treatment redness close-up"></div>
    <div class="result" style="left:400px;background:radial-gradient(circle at 40% 40%,#f0c8bb,#6e4c44)" role="img" aria-label="After treatment redness close-up"></div>
  </div>
</section>

<!-- Booking -->
<section class="page col-r row-3 booking">
  <div class="photo" style="left:330px;top:0;width:228px;height:366px;background:linear-gradient(160deg,#6b4a38,#a88068 40%,#7d7b7c 70%,#3a3a3a)" role="img" aria-label="Portrait of the owner wearing a grey fur wrap"></div>
  <div class="abs booking-info">
    <h2>BOOK ONLINE</h2>
    <div class="line"><svg width="10" height="10" viewBox="0 0 10 10"><rect x="0.5" y="1" width="9" height="6" rx="1" fill="#fff"/><path d="M2 7 L2 9.5 L4.5 7Z" fill="#fff"/></svg>(720) 555-0148</div>
    <div class="line"><svg width="10" height="10" viewBox="0 0 10 10"><circle cx="5" cy="5" r="4.3" fill="none" stroke="#fff"/><ellipse cx="5" cy="5" rx="1.8" ry="4.3" fill="none" stroke="#fff"/><line x1="0.7" y1="5" x2="9.3" y2="5" stroke="#fff"/></svg>www.GlowWithMara.com</div>
    <h2 class="gap">LOCATION:</h2>
    <div class="line"><svg width="10" height="10" viewBox="0 0 10 10"><path d="M5 0.5a3.3 3.3 0 0 1 3.3 3.3C8.3 6.3 5 9.5 5 9.5S1.7 6.3 1.7 3.8A3.3 3.3 0 0 1 5 .5Z" fill="#fff"/><circle cx="5" cy="3.8" r="1.2" fill="#121212"/></svg>Glow With Mara</div>
    <div class="line pad">4120 Aspen Ridge Blvd #210</div>
    <div class="line pad">Cedar Hollow, Colorado 80199</div>
    <h2 class="gap">BY APPT. HOURS:</h2>
    <div class="line"><svg width="10" height="10" viewBox="0 0 10 10"><circle cx="5" cy="5" r="4.5" fill="#fff"/><path d="M5 2.2V5h2.2" stroke="#121212" stroke-width="1" fill="none"/></svg>Monday: 10:00-am-4:00pm</div>
    <div class="line pad">Tuesday: 10:00pm-6:00pm</div>
    <div class="line pad">Wednesday: 10:00am-6:00pm</div>
    <div class="line pad">Thursda: 10:00am-6:00pm</div>
    <div class="line pad">Friday: 10:00am-6:00pm</div>
    <div class="line pad">Saturday: 10:00-4:00pm</div>
    <div class="line pad">Sunday: Closed</div>
  </div>
  <div class="abs booking-name">GLOW WITH MARA</div>
</section>

</body>
</html>
```